Velmora Systems Website

Website design for our company: Velmora Systems.
The website should look fresh and IT focused. Please have a look at http://www.velmorasystems.example.au/ for our current design. We want something fresh and new, professional looking, in WordPress so we can easily make changes.

It Company

```html
<!DOCTYPE html>
<html lang="en">
<head>
<meta charset="utf-8">
<title>Velmora Systems</title>
<link href="https://fonts.googleapis.com/css2?family=Open+Sans:ital,wght@0,400;0,600;1,400&family=Arimo:wght@400;700&display=swap" rel="stylesheet">
<style>
:root{
  --blue:#0b63b1;
  --blue-band:#0d6cb8;
  --green:#14a64b;
  --navy:#061726;
  --ink:#2d2d2d;
  --muted:#555;
  --line:#bdbdbd;
  --footer:#3b3b3b;
  --footer-box:#474747;
}
*{box-sizing:border-box;margin:0;padding:0}
html,body{width:952px;height:1200px;overflow:hidden;background:#fff}
body{position:relative;font-family:"Arimo",Arial,sans-serif;color:var(--ink)}
.abs{position:absolute}
.head-font{font-family:"Open Sans",Arial,sans-serif}

/* header */
.site-header{position:absolute;left:0;top:0;width:952px;height:93px;background:linear-gradient(#fff,#f1f1f1);border-top:2px solid var(--blue);border-bottom:1px solid #ddd}
.brand{position:absolute;display:flex;align-items:center;gap:7px;font-family:"Open Sans",Arial,sans-serif;font-weight:600}
.brand-mark{width:22px;height:22px;background:var(--green)}
.brand-name{color:var(--green);font-size:17px}
.search{left:519px;top:26px;width:148px;height:22px;border:1px solid #ccc;background:#fff;font:italic 10px "Open Sans",sans-serif;color:#666;padding:5px 7px}
.call{left:688px;top:22px;display:flex;gap:6px;align-items:center}
.call small{display:block;font:9px "Open Sans",sans-serif;color:#333}
.call strong{display:block;font:400 16px "Open Sans",sans-serif;color:#222;line-height:1}
.nav{left:321px;top:64px;display:flex;font:11px "Open Sans",sans-serif;color:#333}
.nav span{padding:0 12px;border-left:1px solid #bbb;line-height:14px}
.nav span:first-child{border:0;padding-left:0;color:var(--green)}
.nav span:last-child{padding-right:0}

/* hero */
.hero{left:0;top:93px;width:952px;height:334px;background:var(--navy)}
.hero-photo{left:133px;top:93px;width:686px;height:334px;background:linear-gradient(90deg,#c9ccd0 0%,#e8e6e3 40%,#d9d2cb 55%,#3a3f45 80%,#22272c 100%)}
.hero-arrow{width:30px;height:30px;border-radius:50%;background:#1b1b1b;border:2px solid #555}
.hero-band{left:0;top:389px;width:952px;height:38px;background:rgba(13,108,184,.92);color:#fff;font:400 19px "Open Sans",sans-serif;text-align:center;line-height:38px;letter-spacing:.2px}

/* sections */
.h2{font:600 16px "Open Sans",sans-serif;color:var(--blue)}
.dash{height:0;border-top:1px dashed var(--line)}
.svc{position:absolute;width:124px;text-align:center}
.svc h3{font:600 11px "Open Sans",sans-serif;color:#333;margin-bottom:10px}
.svc h3.on{color:var(--green)}
.svc .ring{width:96px;height:96px;margin:0 auto;border-radius:50%;background:radial-gradient(#fafafa,#e6e6e6);border:1px solid #ddd;display:flex;align-items:center;justify-content:center}
.svc .ring.on{background:#fff;border:4px solid var(--green)}
.svc p{font-size:9.5px;line-height:14px;color:#333;margin-top:17px}
.body-text{font-size:8.6px;line-height:12.6px;color:#333;text-align:justify}
.more{font:700 9px Arimo,sans-serif;color:var(--green)}
.photo-block{background:linear-gradient(90deg,#aeb7c0,#e2dcd6 45%,#5d6570 75%,#cfd6dc)}
.quote{font-size:9.5px;line-height:14.6px;color:#333}
.quote b{font:700 16px Georgia,serif;color:#333;line-height:0}
.cite{font:700 8.6px Arimo,sans-serif;color:#444;text-align:right}
.field{position:absolute;left:608px;width:204px;border:1px solid #c9c9c9;background:#fff;font:italic 9px "Open Sans",sans-serif;color:#777;padding:4px 8px;box-shadow:inset 0 1px 2px rgba(0,0,0,.08)}
.btn{position:absolute;background:var(--green);color:#fff;font:600 10px "Open Sans",sans-serif;text-align:center;border-radius:2px}
.client{position:absolute;top:1024px;font:600 17px "Open Sans",sans-serif;color:#666}

/* footer */
.site-footer{left:0;top:1084px;width:952px;height:116px;background:var(--footer)}
.fbox{position:absolute;top:1100px;height:56px;background:var(--footer-box);border:1px solid #5a5a5a;padding:7px 9px;color:#fff}
.fbox h4{font:600 10.5px "Open Sans",sans-serif;margin-bottom:6px}
.fbox p{font-size:8.6px;line-height:14px;display:flex;align-items:center;gap:6px}
.social{display:inline-block;width:18px;height:18px;margin-right:8px;border-radius:2px}
.links{left:140px;top:1176px;font-size:8.6px;color:#fff}
.links span:first-child{color:var(--green)}
.copy{left:610px;top:1176px;font-size:8.6px;color:#fff}
</style>
</head>
<body>

<header class="site-header">
  <div class="brand" style="left:140px;top:28px"><span class="brand-mark"></span><span class="brand-name">Velmora Systems</span></div>
  <div class="abs search">search
    <svg class="abs" style="right:6px;top:5px" width="11" height="11" viewBox="0 0 11 11"><circle cx="4.5" cy="4.5" r="3.5" fill="none" stroke="#888" stroke-width="1.4"/><path d="M7 7l3 3" stroke="#888" stroke-width="1.6"/></svg>
  </div>
  <div class="abs call">
    <svg width="24" height="24" viewBox="0 0 24 24"><circle cx="12" cy="12" r="10.5" fill="none" stroke="#14a64b" stroke-width="1.6"/><path d="M9 6c-2 1-2 4 0 7s4 5 6 5l1-2-2-2-1 1c-1-1-3-3-3-5l1-1-1-2z" fill="#14a64b"/></svg>
    <div><small>Call Us Today</small><strong>120 555 0148</strong></div>
  </div>
  <nav class="abs nav"><span>HOME</span><span>ABOUT US</span><span>SERVICES</span><span>SUPPORT</span><span>TESTIMONIALS</span><span>CLIENTS</span><span>CONTACT US</span></nav>
</header>

<section>
  <div class="abs hero"></div>
  <div class="abs hero-photo" role="img" aria-label="Smiling engineer on the phone holding a tablet beside server racks and cabling"></div>
  <div class="abs hero-arrow" style="left:143px;top:234px"><svg width="26" height="26" viewBox="0 0 26 26"><path d="M15 8l-5 5 5 5" fill="none" stroke="#fff" stroke-width="1.6"/></svg></div>
  <div class="abs hero-arrow" style="left:779px;top:234px"><svg width="26" height="26" viewBox="0 0 26 26"><path d="M11 8l5 5-5 5" fill="none" stroke="#fff" stroke-width="1.6"/></svg></div>
  <div class="abs hero-band">WE HAVE SPECIALISED ENGINEERS, TRAINED TO DO SPECIALISED WORK</div>
</section>

<section>
  <h2 class="abs h2" style="left:142px;top:457px">Our Services</h2>
  <svg class="abs" style="left:782px;top:465px" width="32" height="12" viewBox="0 0 32 12"><path d="M6 1L1 6l5 5" fill="none" stroke="#555" stroke-width="1.3"/><path d="M23 1l5 5-5 5" fill="none" stroke="#14a64b" stroke-width="1.3"/></svg>
  <div class="abs dash" style="left:142px;top:481px;width:671px"></div>

  <div class="svc" style="left:135px;top:502px"><h3 class="on">On-site Service</h3><div class="ring on">
    <svg width="52" height="52" viewBox="0 0 52 52"><path d="M12 40L32 20M20 12l20 20" stroke="#14a64b" stroke-width="7" stroke-linecap="round"/><path d="M8 16l8-8 6 6-8 8z" fill="#14a64b"/><circle cx="38" cy="14" r="7" fill="#14a64b"/></svg></div>
    <p>Lorem ipsum dolor sit amet ummy nibh eui smod</p></div>
  <div class="svc" style="left:274px;top:502px"><h3>Remote Desktop</h3><div class="ring">
    <svg width="54" height="48" viewBox="0 0 54 48"><rect x="4" y="6" width="30" height="22" fill="none" stroke="#555" stroke-width="3"/><path d="M14 34h12" stroke="#555" stroke-width="3"/><circle cx="36" cy="30" r="13" fill="#eee" stroke="#555" stroke-width="3"/><path d="M31 27l4 3-4 3M41 27l-4 3 4 3" fill="none" stroke="#555" stroke-width="2"/></svg></div>
    <p>Lorem ipsum dolor sit amet ummy nibh eui smod</p></div>
  <div class="svc" style="left:413px;top:502px"><h3>Medical IT Service</h3><div class="ring">
    <svg width="54" height="48" viewBox="0 0 54 48"><path d="M8 6v12a10 10 0 0020 0V6" fill="none" stroke="#555" stroke-width="3"/><path d="M18 28v6a8 8 0 0016 0v-4" fill="none" stroke="#555" stroke-width="3"/><circle cx="34" cy="27" r="4" fill="none" stroke="#555" stroke-width="3"/><circle cx="40" cy="12" r="6" fill="none" stroke="#555" stroke-width="3" stroke-dasharray="3 2"/></svg></div>
    <p>Lorem ipsum dolor sit amet ummy nibh eui smod</p></div>
  <div class="svc" style="left:551px;top:502px"><h3>Pharmacy IT</h3><div class="ring">
    <svg width="54" height="48" viewBox="0 0 54 48"><rect x="6" y="6" width="34" height="28" fill="none" stroke="#555" stroke-width="3"/><path d="M11 26l7-9 6 6 8-10" fill="none" stroke="#555" stroke-width="2.5"/><circle cx="38" cy="32" r="7" fill="#eee" stroke="#555" stroke-width="3"/><path d="M43 37l6 6" stroke="#555" stroke-width="4"/></svg></div>
    <p>Lorem ipsum dolor sit amet ummy nibh eui smod</p></div>
  <div class="svc" style="left:689px;top:502px"><h3>Website Design</h3><div class="ring">
    <svg width="54" height="48" viewBox="0 0 54 48"><rect x="6" y="10" width="40" height="26" fill="none" stroke="#555" stroke-width="3"/><path d="M20 42h12M26 36v6" stroke="#555" stroke-width="3"/><path d="M20 30l16-18 4 4-16 18h-4z" fill="#555"/></svg></div>
    <p>Lorem ipsum dolor sit amet ummy nibh eui smod</p></div>

  <div class="abs" style="left:142px;top:698px;width:671px;height:1px;background:linear-gradient(90deg,transparent,#ddd,transparent)"></div>
</section>

<section>
  <h2 class="abs h2" style="left:140px;top:726px">About Velmora Systems</h2>
  <div class="abs dash" style="left:140px;top:750px;width:204px"></div>
  <div class="abs photo-block" style="left:140px;top:759px;width:202px;height:93px" role="img" aria-label="Business team meeting around a table in an office"></div>
  <p class="abs body-text" style="left:140px;top:857px;width:202px">Velmora Systems is an Adelaide based company with a single objective - to excel in the support and service of all computer and IT needs. We provide a high level of consulting services using the most experienced engineers at a reasonable and fair price. We believe in using a Business Value approach to every</p>
  <span class="abs more" style="left:288px;top:937px">Read More »</span>

  <h2 class="abs h2" style="left:373px;top:726px">Client Testimonials</h2>
  <div class="abs dash" style="left:373px;top:750px;width:207px"></div>
  <p class="abs quote" style="left:370px;top:762px;width:210px"><b>“</b> Nonummy nibh uismod tincidunt ut laoreet dolore magna aliquam erat volutpat. Ut wisi enim ad minim nonummy nibh euismod tincidunt <b>”</b></p>
  <p class="abs cite" style="left:373px;top:807px;width:204px">Darren Holt-QMS</p>
  <p class="abs quote" style="left:370px;top:826px;width:210px"><b>“</b> I have always found the team extremely helpful with their advice over the phone. They also have the ability to access our computers remotely, and can rectify most problems quite swiftly. I have no hesitation in recommending Velmora Systems for all of your IT needs. <b>”</b></p>
  <p class="abs cite" style="left:373px;top:909px;width:207px;line-height:11px">Martin Elwood B.Pharm<br>Corran Lane Pharmacy, Hillbrook</p>
  <span class="abs more" style="left:528px;top:937px">Read More »</span>

  <h2 class="abs h2" style="left:608px;top:726px">Quick Contact</h2>
  <div class="abs dash" style="left:608px;top:750px;width:204px"></div>
  <div class="field" style="top:761px;height:21px">Name</div>
  <div class="field" style="top:793px;height:21px">Email</div>
  <div class="field" style="top:825px;height:21px">Phone</div>
  <div class="field" style="top:857px;height:60px">Message</div>
  <div class="btn" style="left:610px;top:928px;width:51px;height:18px;line-height:18px">Submit</div>
</section>

<section>
  <h2 class="abs h2" style="left:140px;top:979px">Our Clients</h2>
  <svg class="abs" style="left:556px;top:986px" width="28" height="12" viewBox="0 0 28 12"><path d="M6 1L1 6l5 5" fill="none" stroke="#555" stroke-width="1.3"/><path d="M21 1l5 5-5 5" fill="none" stroke="#14a64b" stroke-width="1.3"/></svg>
  <div class="abs dash" style="left:140px;top:1003px;width:446px"></div>
  <span class="client" style="left:142px">Northwind</span>
  <span class="client" style="left:282px">Cloudrun</span>
  <span class="client" style="left:420px">Axiom</span>
  <span class="client" style="left:513px">Relaynet</span>

  <h2 class="abs h2" style="left:604px;top:980px">Remote Support</h2>
  <div class="abs dash" style="left:604px;top:1003px;width:206px"></div>
  <div class="field" style="left:604px;top:1013px;width:202px;height:20px">Enter your 6 digit code</div>
  <div class="btn" style="left:604px;top:1039px;width:73px;height:18px;line-height:18px">Connect Now</div>
</section>

<footer>
  <div class="abs site-footer"></div>
  <div class="fbox" style="left:140px;width:184px"><h4>Subscribe to Newsletter</h4>
    <div style="display:flex;gap:6px"><div style="width:135px;height:20px;background:#5b5b5b;font:italic 9px 'Open Sans',sans-serif;color:#eee;padding:4px 7px">Email here</div>
    <div style="width:23px;height:20px;background:#5b5b5b"><svg width="23" height="20" viewBox="0 0 23 20"><path d="M9 5l5 5-5 5" fill="none" stroke="#fff" stroke-width="2.4"/></svg></div></div>
  </div>
  <div class="fbox" style="left:363px;width:162px"><h4>Contact Us</h4>
    <p><svg width="9" height="9" viewBox="0 0 9 9"><path d="M2 0c-2 1-2 3 0 6s3 3 5 3l1-1-2-2-1 1C4 6 3 5 3 4l1-1z" fill="#fff"/></svg>120 555 0148</p>
    <p><svg width="9" height="7" viewBox="0 0 9 7"><rect width="9" height="7" fill="#fff"/><path d="M0 0l4.5 4 4.5-4" fill="none" stroke="#474747"/></svg>support@velmorasystems.example.au</p>
  </div>
  <div class="fbox" style="left:564px;width:89px"><h4>Follow Us</h4>
    <div><span class="social" style="background:#5a7fb8"></span><span class="social" style="background:#5bb3df"></span><span class="social" style="background:#e8792b;margin:0"></span></div>
  </div>
  <div class="brand" style="left:692px;top:1118px;gap:6px"><span class="brand-mark" style="width:18px;height:18px;background:#fff"></span><span class="brand-name" style="color:#fff;font-size:14px">Velmora Systems</span></div>
  <p class="abs links"><span>Home</span> | About Us | Services | Support | Testimonials | Clients | Contact Us | Terms Conditions</p>
  <p class="abs copy">Copyright © 2014 velmorasystems. All Rights Reserved</p>
</footer>

</body>
</html>
```